Dental Office Needs Exciting New Stationary

We need a stationary design that incorporates the logo that we already have and would like to keep the existing color scheme. We need something clean and professional. This is a Endodontic (root canals) office and must represent a dental specialist's office. I need a design for a business card, envelope, and letterhead that all coordinate. I would like the business card to incorporate the information in the business card sample that I am providing. I made the business card design myself but would like to see a better one.
Dental

```html
<!DOCTYPE html>
<html lang="en">
<head>
<meta charset="utf-8">
<title>Harbor Endodontics – Business Cards</title>
<link rel="stylesheet" href="https://fonts.googleapis.com/css2?family=Open+Sans:wght@300;400;600;700&display=swap">
<style>
  :root {
    --blue-deep: #1f3f9e;
    --blue-mid: #2460c4;
    --blue-bright: #1e8fd8;
    --grey-text: #8c8f94;
    --grey-line: #b9bcc1;
    --ink: #4a4d52;
    --paper: #ffffff;
    --stage: #ebe8e3;
  }
  html, body {
    margin: 0;
    padding: 0;
    width: 1200px;
    height: 1024px;
    overflow: hidden;
    background: var(--stage);
    font-family: "Open Sans", Arial, sans-serif;
  }
  .sheet {
    width: 1200px;
    height: 1024px;
    display: flex;
    flex-direction: column;
    align-items: center;
    justify-content: center;
    gap: 40px;
  }
  .card {
    position: relative;
    width: 800px;
    height: 457px;
    overflow: hidden;
    box-shadow: 0 6px 18px rgba(0,0,0,0.18);
  }
  /* Front */
  .card-front { background: var(--paper); }
  .card-front .swoosh { position: absolute; inset: 0; }
  .wordmark {
    font-weight: 700;
    letter-spacing: 0.04em;
    text-transform: uppercase;
    display: flex;
    align-items: center;
    gap: 14px;
    white-space: nowrap;
  }
  .wordmark .dot {
    width: 16px; height: 16px; border-radius: 50%;
  }
  .front-wordmark {
    position: absolute;
    left: 60px; top: 58px;
    font-size: 34px;
    color: var(--blue-mid);
  }
  .front-wordmark .dot { background: var(--blue-mid); }
  .divider {
    position: absolute;
    left: 400px; top: 150px;
    width: 2px; height: 150px;
    background: linear-gradient(to bottom, rgba(36,96,196,0), var(--blue-mid), rgba(36,96,196,0));
  }
  .doctor {
    position: absolute;
    top: 150px;
    font-size: 14px;
    line-height: 1.55;
    color: var(--ink);
  }
  .doctor-left { left: 60px; }
  .doctor-right { left: 440px; }
  .doctor .name {
    font-size: 17px;
    font-weight: 600;
    color: var(--blue-mid);
    margin-bottom: 6px;
  }
  .doctor .cred {
    color: var(--grey-text);
    font-weight: 700;
    padding-left: 8px;
    margin-left: 6px;
    border-left: 2px solid var(--grey-line);
  }
  .doctor .label { color: var(--blue-mid); font-weight: 600; }
  .doctor .address { margin-top: 4px; text-transform: uppercase; font-size: 13px; }
  .front-web {
    position: absolute;
    left: 60px; bottom: 22px;
    color: var(--paper);
    font-size: 15px;
    letter-spacing: 0.03em;
  }
  /* Back */
  .card-back {
    background: radial-gradient(ellipse at 70% 40%, var(--blue-bright) 0%, var(--blue-mid) 50%, var(--blue-deep) 100%);
  }
  .back-glow {
    position: absolute; inset: 0;
    background: radial-gradient(circle at 35% 65%, rgba(255,255,255,0.08) 0%, rgba(255,255,255,0) 45%);
  }
  .back-wordmark {
    position: absolute;
    left: 50%; top: 50%;
    transform: translate(-50%, -50%);
    font-size: 46px;
    color: var(--paper);
  }
  .back-wordmark .dot { background: var(--paper); width: 22px; height: 22px; }
  .back-web {
    position: absolute;
    left: 0; right: 0; bottom: 40px;
    text-align: center;
    color: var(--paper);
    font-size: 15px;
    letter-spacing: 0.05em;
  }
</style>
</head>
<body>
<main class="sheet">

  <section class="card card-front" aria-label="Business card front">
    <svg class="swoosh" width="800" height="457" viewBox="0 0 800 457" aria-hidden="true">
      <defs>
        <linearGradient id="bandBlue" x1="0" y1="1" x2="1" y2="0">
          <stop offset="0" stop-color="#1f3f9e"/>
          <stop offset="0.6" stop-color="#2460c4"/>
          <stop offset="1" stop-color="#1e8fd8"/>
        </linearGradient>
      </defs>
      <path d="M0 378 C 260 420, 560 400, 800 270" fill="none" stroke="#b9bcc1" stroke-width="8"/>
      <path d="M0 398 C 260 440, 560 420, 800 292 L800 457 L0 457 Z" fill="url(#bandBlue)"/>
    </svg>

    <div class="wordmark front-wordmark"><span class="dot"></span>Harbor Endodontics</div>

    <div class="doctor doctor-left">
      <div class="name">Daniel R Whitcomb<span class="cred">DDS MS</span></div>
      <div><span class="label">O:</span> 555.310.2366</div>
      <div><span class="label">F:</span> 555.310.5929</div>
      <div class="address">482 Elm Street<br>Riverton, CA 95000</div>
    </div>

    <div class="divider"></div>

    <div class="doctor doctor-right">
      <div class="name">Marco L Reyes<span class="cred">DDS</span></div>
      <div><span class="label">O:</span> 555.208.1101</div>
      <div><span class="label">F:</span> 555.208.0602</div>
      <div class="address">3150 Linden Ave. Suite #2<br>Fairview, CA 95600</div>
    </div>

    <div class="front-web">www.Harborendo.com</div>
  </section>

  <section class="card card-back" aria-label="Business card back">
    <div class="back-glow"></div>
    <div class="wordmark back-wordmark"><span class="dot"></span>Harbor Endodontics</div>
    <div class="back-web">www.Harborendo.com</div>
  </section>

</main>
</body>
</html>
```